BRINDLEWOOD EXTRA VIRGIN OLIVE OIL

I needs a design for an Australian Extra Virgin Olive Oil.

The label will go on a round clear bottle

The label size front and back is 145mm high x 60mm wide.

The important points for the design are as follows.

I want to see elegant olives on the label so that non English speaking markets can easily understand its olive oil. I want it too look classy . IT must also look Australian but I don't want to see kangaroos just colours that reflect Australia.

The mandatory info on front label will be

BRINDLEWOOD

Cold Pressed
EXTRA VIRGIN OLIVE OIL

AUSTRALIAN

1 litre

```html
<!DOCTYPE html>
<html lang="en">
<head>
<meta charset="utf-8">
<title>Brindlewood | Extra Virgin Oil Label</title>
<link rel="stylesheet" href="https://fonts.googleapis.com/css2?family=Fira+Sans:wght@300;400&display=swap">
<style>
  :root {
    --paper: #ffffff;
    --ink: #2b2b2b;
    --rule: #9a9a9a;
    --dim: #c4c4c4;
    --ochre: #c8632a;
    --earth: #3a2314;
    --grey-text: #6e6a67;
    --olive-dark: #5a4b45;
    --oil-light: #dcc36a;
    --oil-deep: #b08a22;
  }
  * { margin: 0; padding: 0; box-sizing: border-box; }
  html, body { width: 1200px; height: 848px; overflow: hidden; background: var(--paper); }
  body { font-family: "Fira Sans", sans-serif; color: var(--ink); position: relative; }

  .sheet-header {
    position: absolute; left: 56px; top: 30px; width: 1081px; height: 21px;
    border-top: 1px solid var(--ink); border-bottom: 1px solid var(--ink);
    display: flex; justify-content: space-between; align-items: center;
    font-size: 12.5px; letter-spacing: 0.09em; font-weight: 400;
  }
  .sheet-footer {
    position: absolute; left: 56px; top: 810px; width: 1081px;
    border-top: 1px solid var(--rule);
  }

  .dimension { position: absolute; color: var(--dim); font-size: 9.5px; }
  .dimension-width { height: 28px; border-bottom: 1px solid var(--dim); border-left: 1px solid var(--dim); border-right: 1px solid var(--dim); text-align: center; }
  .dimension-width span { position: relative; top: 1px; }
  .dimension-height { width: 12px; border-left: 1px solid var(--dim); border-top: 1px solid var(--dim); border-bottom: 1px solid var(--dim); }
  .dimension-height span { position: absolute; left: -11px; top: 50%; transform: translateY(-50%) rotate(-90deg); }

  .label { position: absolute; top: 161px; width: 241px; height: 582px; }
  .label-light { background: var(--paper); border: 1px solid #d6d6d6; }
  .label-dark { background: var(--earth); }

  .label > div { position: absolute; line-height: 1; white-space: nowrap; }
  .brand { left: 25px; top: 112px; font-size: 24px; font-weight: 400; letter-spacing: 0.02em; }
  .brand-rule { left: 26px; top: 148px; width: 171px; height: 1px; }
  .process { left: 26px; top: 163px; font-size: 13px; font-weight: 300; }
  .product { left: 26px; top: 178px; font-size: 18px; font-weight: 400; }
  .origin { left: 26px; top: 214px; font-size: 17px; font-weight: 300; }
  .volume { left: 28px; top: 543px; font-size: 13px; font-weight: 300; }
  .label > .olive-sprig { left: 158px; top: 486px; width: 64px; height: 75px; }

  .label-light .brand { color: var(--ochre); }
  .label-light .brand-rule { background: var(--rule); }
  .label-light .process, .label-light .origin { color: var(--grey-text); }
  .label-light .product { color: #3e3a37; }
  .label-light .volume { color: var(--ochre); }
  .label-light .olive-sprig { background: var(--olive-dark); }

  .label-dark .brand, .label-dark .product { color: #ffffff; }
  .label-dark .brand-rule { background: #d9d1cb; }
  .label-dark .process, .label-dark .origin, .label-dark .volume { color: #d6ccc5; }
  .label-dark .olive-sprig { background: #ffffff; }

  .bottle-photo {
    position: absolute; top: 111px; height: 639px;
    background: linear-gradient(90deg, var(--oil-deep), var(--oil-light) 50%, var(--oil-deep));
  }

  .label-tag {
    position: absolute; top: 778px; width: 40px; height: 16px;
    background: var(--earth); color: #ffffff; border-radius: 3px;
    font-size: 9px; text-align: center; line-height: 16px;
  }
</style>
</head>
<body>
  <header class="sheet-header">
    <span>BRINDLEWOOD &nbsp;|&nbsp; EXTRA VIRGIN OIL LABEL - 145x60 mm</span>
    <span>27.FEB.2013</span>
  </header>

  <div class="dimension dimension-width" style="left:98px; top:123px; width:241px;"><span>60</span></div>
  <div class="dimension dimension-height" style="left:62px; top:161px; height:582px;"><span>145</span></div>
  <section class="label label-light" style="left:98px;">
    <div class="brand">BRINDLEWOOD</div>
    <div class="brand-rule"></div>
    <div class="process">Cold Pressed</div>
    <div class="product">Extra virgin Olive Oil</div>
    <div class="origin">Australian</div>
    <div class="volume">1 litre</div>
    <div class="olive-sprig" role="img" aria-label="Illustration of an olive sprig with three olives and leaves"></div>
  </section>
  <div class="bottle-photo" style="left:400px; width:137px;" role="img" aria-label="Photograph of a clear round olive oil bottle wearing the white label"></div>
  <div class="label-tag" style="left:188px;">Label 1</div>

  <div class="dimension dimension-width" style="left:700px; top:123px; width:241px;"><span>60</span></div>
  <div class="dimension dimension-height" style="left:664px; top:161px; height:582px;"><span>145</span></div>
  <section class="label label-dark" style="left:700px;">
    <div class="brand">BRINDLEWOOD</div>
    <div class="brand-rule"></div>
    <div class="process">Cold Pressed</div>
    <div class="product">Extra virgin Olive Oil</div>
    <div class="origin">Australian</div>
    <div class="volume">1 litre</div>
    <div class="olive-sprig" role="img" aria-label="White illustration of an olive sprig with three olives and leaves"></div>
  </section>
  <div class="bottle-photo" style="left:1002px; width:135px;" role="img" aria-label="Photograph of a clear round olive oil bottle wearing the brown label"></div>
  <div class="label-tag" style="left:790px;">Label 2</div>

  <footer class="sheet-footer"></footer>
</body>
</html>
```